Vibrant, yet professional, stationery set and other designs required.

I need to source a fantastic designer for a new project as part of my company using a new logo designed via sketch harbor.

**UPDATE** I am not looking for just 'fine' design that will suffice. I am looking for something great.

We are a life assurance brokerage based in Dublin, Ireland and BrightRoost.ie is our new website aimed at providing services for young families in Ireland. We are hoping to be the 'Velro' level of service providers in this area and I am looking for the quality of design to reflect this :-) Hopefully that makes sense!

I have a preference for straight lines over curves and waves.

I need...

1. Business card
2. Letterhead
3. Banner (for printing - 76cm X 305cm)
4. Car branding for KORVA 9 (2014 sport model) I believe the templates are freely available online.

Target Market(s)

Parents in Ireland - Aged 27 to 50.

Industry/Entity Type

Financial Planning

Colors

Designer to choose colors to be used in the design.

Requirements
Must have
• All of the items listed in the description above. I like clean, bright, legible, vibrant and professional design.
Should not have
• No silly or 'cheap' looking designs. This is a professional company looking to provide a professional service.

```html
<!DOCTYPE html>
<html lang="en">
<head>
<meta charset="UTF-8">
<title>BrightRoost.ie — Business Card</title>
<link rel="stylesheet" href="https://fonts.googleapis.com/css2?family=Exo+2:wght@600&family=Roboto:wght@400;500&display=swap">
<style>
  :root {
    --backdrop: #c9c9c9;
    --brand-orange: #f08019;
    --card-white: #f7f7f7;
    --logo-grey: #7e8b91;
    --text-dark: #555a5d;
    --band-grey: #8c9699;
    --title-grey: #8f9a9e;
  }
  html, body {
    margin: 0;
    width: 1200px;
    height: 960px;
    overflow: hidden;
    background: var(--backdrop);
  }
  .canvas {
    position: relative;
    width: 1200px;
    height: 960px;
  }
  .card {
    position: absolute;
    left: 320px;
    width: 600px;
    height: 342px;
    box-shadow: 0 3px 8px rgba(0,0,0,0.25);
    overflow: hidden;
  }
  .card--front {
    top: 104px;
    background: var(--brand-orange);
  }
  .card--back {
    top: 493px;
    background: var(--card-white);
  }
  .wordmark {
    position: absolute;
    left: 0;
    right: 0;
    text-align: center;
    font-family: "Exo 2", "Roboto", sans-serif;
    font-weight: 600;
    letter-spacing: -0.5px;
    white-space: nowrap;
  }
  .card--front .wordmark {
    top: 128px;
    font-size: 62px;
    color: #ffffff;
  }
  .card--back .wordmark {
    top: 86px;
    font-size: 58px;
    color: var(--logo-grey);
  }
  .contact {
    position: absolute;
    left: 0;
    right: 0;
    top: 205px;
    text-align: center;
    font-family: "Roboto", sans-serif;
    color: var(--text-dark);
    font-size: 14px;
    line-height: 21px;
  }
  .contact p { margin: 0; }
  .contact__name {
    font-size: 19px;
    font-weight: 500;
    color: var(--brand-orange);
    line-height: 26px;
  }
  .contact__title {
    font-size: 14px;
    font-weight: 400;
    color: var(--title-grey);
  }
  .contact__label {
    color: var(--brand-orange);
  }
  .contact__web {
    letter-spacing: 3.5px;
    font-weight: 500;
    font-size: 13px;
  }
  .card__band {
    position: absolute;
    left: 0;
    right: 0;
    bottom: 0;
    height: 12px;
    background: var(--band-grey);
  }
</style>
</head>
<body>
  <main class="canvas">
    <section class="card card--front" aria-label="Business card front">
      <div class="wordmark">BrightRoost.ie</div>
    </section>

    <section class="card card--back" aria-label="Business card back">
      <div class="wordmark">BrightRoost.ie</div>
      <div class="contact">
        <p class="contact__name">Liam Carver - <span class="contact__title">CEO/Founder</span></p>
        <p class="contact__address">42 Larkfield Row, Ranelagh, Dublin D06 K2P1</p>
        <p class="contact__lines"><span class="contact__label">P :</span> 601 284 7195 <span class="contact__label">E</span> : hello@brightroost.ie</p>
        <p class="contact__web">www.brightroost.ie</p>
      </div>
      <div class="card__band"></div>
    </section>
  </main>
</body>
</html>
```